Velmora Consulting Business

** Please add the content information from my old business card
1. I would like to see a two sided business card with both options with the 1st Option--Tallow Spire-new WHITE BACKGROUND LOGO
2 nd Option-Tallow Spire - new BLACK- Background Logo
3rd -Option a business card with my Photo on the card
Please add the new word to the card information:
EXECUTION
AS THE OWNER'S REP
WE AIM TO ACHIEVE YOUR
INFRASTRUCTURE VISION with
OUR SPECIALIZATION & EXECUTION in:

FUNDING Planning
BUSINESS Planning
INFRASTRUCTURE Planning
PROJECT Management
Since 2012
_____________________________________________________________________
I want to get spot uv raised printing. I was liking a a nice rich white linen paper stock with black writing & NOT A COLORED CARD other than a variety of white or black cards concept

```html
<!DOCTYPE html>
<html lang="en">
<head>
<meta charset="utf-8">
<title>Velmora Consulting – Business Card</title>
<link rel="stylesheet" href="https://fonts.googleapis.com/css2?family=Arimo:wght@400;700&display=swap">
<style>
  :root {
    --backdrop: #1b1b1b;
    --paper: #f3f3f3;
    --ink: #262626;
    --ink-soft: #2f2f2f;
    --dark-card: #2a2a2c;
    --accent: #e0203a;
    --light-text: #f2f2f2;
    --brand-faint: #4a4a4c;
  }
  * { margin: 0; padding: 0; box-sizing: border-box; }
  html, body { width: 1200px; height: 1059px; overflow: hidden; }
  body {
    background: var(--backdrop);
    font-family: "Arimo", Arial, sans-serif;
    position: relative;
  }
  .card {
    position: absolute;
    border-radius: 22px;
    overflow: hidden;
    box-shadow: 0 10px 24px rgba(0,0,0,.55);
  }

  /* Front */
  .card-front { left: 257px; top: 89px; width: 687px; height: 390px; background: var(--paper); }
  .front-band { position: absolute; left: 0; top: 0; width: 687px; height: 390px; }
  .brand-block {
    position: absolute; left: 74px; top: 196px;
    width: 220px; text-align: center;
    color: var(--ink); font-weight: 700;
  }
  .brand-name { font-size: 46px; line-height: 1; letter-spacing: -0.5px; }
  .brand-sub { font-size: 12px; letter-spacing: 10px; margin-top: 10px; padding-left: 10px; font-weight: 700; }
  .brand-dot {
    position: absolute; left: 276px; top: 190px;
    width: 12px; height: 12px; border-radius: 50%; background: var(--accent);
  }
  .divider { position: absolute; left: 306px; top: 94px; width: 1.5px; height: 167px; background: var(--ink); }
  .details { position: absolute; left: 333px; top: 90px; color: var(--ink-soft); }
  .person-name { color: var(--accent); font-weight: 700; font-size: 24px; line-height: 1; }
  .person-title { font-size: 15.5px; margin-top: 9px; letter-spacing: .2px; }
  .contact-list { list-style: none; margin-top: 15px; }
  .contact-list li { display: flex; align-items: center; font-size: 17px; height: 25.5px; }
  .contact-list svg { width: 13px; height: 13px; margin-right: 7px; fill: var(--accent); }
  .locations { font-size: 16.5px; margin-top: 13px; }

  /* Back */
  .card-back { left: 254px; top: 547px; width: 693px; height: 393px; background: var(--dark-card); text-align: center; }
  .back-brand { position: absolute; left: 0; right: 0; top: 58px; color: var(--brand-faint); font-weight: 700; }
  .back-brand .brand-name { font-size: 62px; }
  .back-brand .brand-sub { font-size: 16px; letter-spacing: 16px; padding-left: 16px; margin-top: 8px; }
  .pitch { position: absolute; left: 0; right: 0; top: 163px; color: var(--light-text); font-size: 18.5px; line-height: 30.5px; }
  .pitch .lead { color: var(--accent); }
  .rule { position: absolute; left: 0; width: 100%; height: 1.5px; background: var(--accent); }
  .rule-top { top: 257px; }
  .rule-bottom { top: 354px; }
  .services { position: absolute; left: 0; right: 0; top: 271px; color: var(--light-text); font-size: 18.5px; line-height: 32px; }
  .services .sep { color: var(--accent); margin: 0 6px; }
  .since {
    position: absolute; left: 288px; top: 342px; width: 116px; height: 25px;
    border: 1.5px solid var(--accent); border-radius: 13px;
    background: var(--dark-card); color: var(--light-text);
    font-size: 18px; line-height: 22px;
  }
</style>
</head>
<body>

<section class="card card-front">
  <svg class="front-band" viewBox="0 0 687 390" aria-hidden="true">
    <path d="M0 327 Q343 400 687 327 L687 390 L0 390 Z" fill="var(--ink)"/>
    <path d="M38 332 Q343 393 649 332 Q343 376 38 332 Z" fill="var(--accent)"/>
  </svg>

  <div class="brand-block">
    <div class="brand-name">Velmora</div>
    <div class="brand-sub">CONSULTING</div>
  </div>
  <span class="brand-dot"></span>

  <div class="divider"></div>

  <div class="details">
    <h1 class="person-name">Marisol Fenwick-Adair</h1>
    <p class="person-title">CEO / LEAD PROJECT MANAGER</p>
    <ul class="contact-list">
      <li><svg viewBox="0 0 16 16"><path d="M1 6 Q8 0 15 6 L12 8 L11 6 Q8 5 5 6 L4 8 Z M3 9 H13 L14 14 H2 Z"/></svg>867.555.0142</li>
      <li><svg viewBox="0 0 16 16"><path d="M1 6 L8 1 L15 6 V15 H1 Z M3 7 L8 11 L13 7 V5 H3 Z"/></svg>marisol@velmora.ca</li>
      <li><svg viewBox="0 0 16 16"><circle cx="8" cy="8" r="7"/></svg>www.velmora.ca</li>
    </ul>
    <p class="locations">Norvale NT • Brackenford NB</p>
  </div>
</section>

<section class="card card-back">
  <div class="back-brand">
    <div class="brand-name">Velmora</div>
    <div class="brand-sub">CONSULTING</div>
  </div>

  <p class="pitch">
    <span class="lead">AS THE OWNER'S REP</span><br>
    WE AIM TO ACHIEVE YOUR INFRASTRUCTURE VISION<br>
    with OUR SPECIALIZATION &amp; EXECUTION in:
  </p>

  <div class="rule rule-top"></div>

  <p class="services">
    FUNDING Planning<span class="sep">|</span>BUSINESS Planning<br>
    INFRASTRUCTURE Planning<span class="sep">|</span>PROJECT Management
  </p>

  <div class="rule rule-bottom"></div>
  <div class="since">Since 2012</div>
</section>

</body>
</html>
```